Stage Design Company Business Card

We are looking to step up up our business card design for our team.

We are a Full service Design and Consultation company for Stage and TV with an emphasis in Theatrical Lighting.

We like our materials to be clean and modern with solid colors free of patterns and gradients. Our brand consists of 4 primary colors Purple, Black, Grey, and White. Provided is our Word Mark as well as our Symbol Logo.

We would like our cards to leave an impression beyond the information, show our attention to design and detail, and make our marks an easily recognized feature (together or apart) for our clients.

We need a warm approachable comfortable feel for some clients, and a professional flair for the board member type clients.

Attached are our brand elements, and our existing cards to give a sense of our style and a glipse at the information we provide on our cards.

Target Market(s)

broad client base from church leaders to high school teachers and architects.

Industry/Entity Type

Business

Contact Information for Business Card

We format our phone number with periods not parenthesis or dashes. Information will be edited for each of our team members, and team member specific cards are not part of this scope, but rather a template so to speak.

Font styles to use
Sans Serif

Colors
6b449b
ffffff
000000
333333
aaaaaa

Requirements
Must have
• Wordmark and logo mark present (does not need to exist on the same side of card)
• Brand Colors,
• Name, Phone, Email, Address.
• Unique choices that make someone stop and take a second look
Nice to have
• It would be nice to somehow convey what we DO, as our brand name does not lend itself to this, outside of an obvious tagline though.....
• social media if not crowded. all of our handles match (instagram, twitter, facebook)
Should not have
• "clipart"

```html
<!DOCTYPE html>
<html lang="en">
<head>
<meta charset="utf-8">
<title>Harlow Staging – Business Card</title>
<link rel="stylesheet" href="https://fonts.googleapis.com/css2?family=Montserrat:wght@400;700&family=Questrial&display=swap">
<style>
  :root {
    --backdrop: #161616;
    --paper: #fbf8f4;
    --ink: #111111;
    --grey: #aaaaaa;
    --text: #444444;
    --purple: #3b2a6b;
    --white: #ffffff;
  }
  * { box-sizing: border-box; margin: 0; padding: 0; }
  html, body {
    width: 1200px; height: 1000px; overflow: hidden;
    background: var(--backdrop);
  }
  .canvas {
    position: relative; width: 1200px; height: 1000px;
  }
  .card {
    position: absolute; top: 357px;
    width: 500px; height: 286px;
    background: var(--paper);
    box-shadow: 0 6px 18px rgba(0,0,0,0.45);
    overflow: hidden;
  }
  .card--front { left: 70px; }
  .card--back { left: 630px; }

  /* Front: wordmark */
  .wordmark {
    position: absolute; top: 50%; left: 50%;
    transform: translate(-50%, -50%);
    text-align: center;
  }
  .wordmark__name {
    font-family: "Montserrat", sans-serif; font-weight: 700;
    font-size: 44px; letter-spacing: 20px; color: var(--ink);
    margin-right: -20px;
  }
  .wordmark__tag {
    margin-top: 8px;
    font-family: "Montserrat", sans-serif; font-weight: 700;
    font-size: 13px; letter-spacing: 15px; color: var(--grey);
    margin-right: -15px;
  }

  /* Back */
  .accent-panel {
    position: absolute; inset: 0;
    background: var(--purple);
    clip-path: polygon(53% 30%, 100% 30%, 100% 100%, 46% 100%);
  }
  .contact {
    position: absolute; left: 30px; top: 78px;
    font-family: "Questrial", sans-serif; color: var(--text);
    font-size: 13px; line-height: 1.3;
  }
  .contact__name {
    font-family: "Montserrat", sans-serif; font-weight: 700;
    font-size: 17px; color: var(--purple); margin-bottom: 8px;
  }
  .contact__group + .contact__group { margin-top: 6px; }
  .social {
    position: absolute; right: 28px; top: 40px;
    display: flex; align-items: center; gap: 8px;
    font-family: "Montserrat", sans-serif; font-weight: 700;
    font-size: 13px; color: var(--purple); letter-spacing: 0.5px;
  }
  .social__mark {
    width: 10px; height: 10px; background: var(--purple);
  }
  .symbol {
    position: absolute; right: 40px; bottom: 50px;
    display: flex; align-items: center; gap: 10px;
    font-family: "Montserrat", sans-serif; font-weight: 700;
    font-size: 22px; letter-spacing: 3px; color: var(--white);
  }
  .symbol__dot {
    width: 18px; height: 18px; border-radius: 50%; background: var(--white);
  }
</style>
</head>
<body>
<main class="canvas">
  <section class="card card--front" aria-label="Card front">
    <div class="wordmark">
      <div class="wordmark__name">HARLOW</div>
      <div class="wordmark__tag">STAGING</div>
    </div>
  </section>

  <section class="card card--back" aria-label="Card back">
    <div class="accent-panel"></div>
    <div class="social">
      <span class="social__mark"></span>
      <span>HARLOW-S</span>
    </div>
    <div class="contact">
      <div class="contact__name">Owen R Harlow</div>
      <div class="contact__group">
        800.555.0142<br>
        owen@harlow-s.com<br>
        harlow-s.com
      </div>
      <div class="contact__group">
        52 N Center St Tempe<br>
        AZ 85281
      </div>
    </div>
    <div class="symbol">
      <span class="symbol__dot"></span>
      <span>HARLOW</span>
    </div>
  </section>
</main>
</body>
</html>
```